Website for BrightlineLabs presentation

We need a new website, ideally as a wordpress there, for BrightlineLabs - we focus on machine learning, big data, data science and data analytics. This website should have two main sections - team presentation, introduction and offered services as static pages, and a blog section.

Target Market(s)

Companies which would like to hire the consultants for data science

Industry/Entity Type

Data Service

Font styles to use
Sans Serif

Colors

Designer to choose colors to be used in the design.

Requirements
Must have
• Wordpress template, blog and presentation pages, nice background images, incorporate the existing logo from brief
Nice to have
• match the word and ppt existing templates for brightline labs

```html
<!DOCTYPE html>
<html lang="en">
<head>
<meta charset="utf-8">
<title>Brightline Labs</title>
<link href="https://fonts.googleapis.com/css2?family=Lato:ital,wght@0,300;0,400;0,700;0,900;1,400&display=swap" rel="stylesheet">
<style>
:root{
  --blue:#1784c7;
  --blue-light:#2a9ad8;
  --ink:#3f3f3f;
  --grey:#6d6d6d;
  --muted:#9a9a9a;
  --line:#d6d6d6;
  --dark:#05080f;
  --white:#ffffff;
  --contact:#4ea7d6;
}
*{margin:0;padding:0;box-sizing:border-box}
html,body{width:1200px;height:3066px;overflow:hidden}
body{font-family:"Lato",sans-serif;color:var(--ink);background:var(--white);position:relative}
section,header,footer{position:absolute;left:0;width:1200px}

/* header */
.site-header{top:0;height:146px;background:var(--white)}
.brand{position:absolute;left:78px;top:42px;display:flex;align-items:center;gap:14px}
.brand-mark{width:46px;height:46px;border-radius:50%;background:var(--blue)}
.brand-name{font-weight:900;font-size:25px;line-height:26px;color:var(--blue);width:150px}
.main-nav{position:absolute;left:318px;top:60px;display:flex;font-size:16px;color:#8a8a8a}
.main-nav a{color:inherit;text-decoration:none;margin-right:48px}
.nav-divider{position:absolute;left:792px;top:58px;width:1px;height:22px;background:#999}
.nav-phone{position:absolute;left:815px;top:60px;display:flex;align-items:center;gap:12px;font-size:18px;color:#222}
.login-btn{position:absolute;left:998px;top:49px;width:124px;height:49px;border-radius:25px;background:var(--blue);color:var(--white);font-weight:700;font-size:16px;display:flex;align-items:center;justify-content:center;gap:10px}

/* hero */
.hero{top:146px;height:574px;background:linear-gradient(90deg,#dbe9f2 0%,#c2d9e7 40%,#6f95ad 70%,#1f3a55 100%)}
.hero-photo{position:absolute;right:0;top:0;width:660px;height:574px;background:linear-gradient(135deg,rgba(255,255,255,0) 0%,rgba(20,45,75,.55) 55%,rgba(10,25,45,.8) 100%)}
.hero-title{position:absolute;left:78px;top:158px;font-weight:900;font-size:43px;color:var(--blue);letter-spacing:.5px}
.hero-text{position:absolute;left:80px;top:224px;width:462px;font-size:15px;line-height:25px;color:#2a2a2a}
.btn{display:inline-flex;align-items:center;justify-content:center;font-size:16px;text-transform:uppercase}
.hero-actions{position:absolute;left:78px;top:324px;display:flex;gap:12px}
.btn-solid{background:var(--blue);color:var(--white);width:156px;height:60px}
.btn-light{background:var(--white);color:var(--blue);width:156px;height:60px}

/* section headings */
.section-heading{position:absolute;left:0;width:1200px;display:flex;align-items:center;justify-content:center;gap:26px;font-weight:700;font-size:38px}
.section-heading::before,.section-heading::after{content:"";width:76px;height:2px;background:currentColor;opacity:.35}
.section-heading em{font-style:normal;color:var(--blue)}

/* about */
.about{top:720px;height:375px}
.about .section-heading{top:56px;color:#4a4a4a}
.about-text{position:absolute;left:260px;top:118px;width:680px;text-align:center;font-size:14px;line-height:25px;color:var(--grey)}
.about .btn-solid{position:absolute;left:522px;top:250px}

/* services */
.services{top:1095px;height:470px;background:linear-gradient(180deg,#030509 0%,#0b1a2a 50%,#04070d 100%)}
.services-bg{position:absolute;inset:0;background:linear-gradient(90deg,rgba(10,30,50,0),rgba(30,70,110,.35) 50%,rgba(10,30,50,0))}
.services .section-heading{top:60px;color:var(--white)}
.services .section-heading em{color:var(--white)}
.service{position:absolute;top:140px;width:260px;text-align:center}
.service svg{display:block;margin:0 auto}
.service h3{font-weight:400;font-size:25px;color:var(--blue-light);margin-top:12px}
.service p{font-size:14px;line-height:25px;color:var(--white);margin:8px auto 0;width:225px}

/* blog */
.blog{top:1565px;height:645px}
.blog .section-heading{top:52px;color:#4a4a4a}
.post{position:absolute;top:155px;width:312px;height:418px;border-radius:26px;background:var(--white);box-shadow:0 4px 16px rgba(0,0,0,.13);padding:0 22px}
.post-meta{margin-top:54px;font-style:italic;font-size:13px;color:#333}
.post-meta span{margin:0 14px}
.post h3{margin-top:30px;font-weight:400;font-size:22px;line-height:30px;color:var(--blue)}
.post p{margin-top:18px;font-size:13px;line-height:25px;color:var(--muted);height:75px;width:250px;overflow:hidden}
.post hr{border:0;height:1px;background:var(--line);width:132px;margin-top:18px}
.author{display:flex;align-items:center;gap:18px;margin-top:24px}
.avatar{width:78px;height:78px;border-radius:50%;background:radial-gradient(circle at 50% 40%,#c9a993,#5a4a44 70%,#33343b)}
.author span{font-size:14px;color:var(--blue);text-transform:uppercase;font-weight:700}

/* contact */
.contact{top:2210px;height:520px;background:linear-gradient(90deg,#58acd9,#3f98cc 50%,#5aaed9)}
.contact-photo{position:absolute;left:300px;top:0;width:600px;height:520px;background:linear-gradient(180deg,rgba(20,60,100,.25),rgba(20,60,100,.05))}
.contact .section-heading{top:40px;color:var(--white)}
.contact .section-heading em{color:var(--white)}
.field{position:absolute;background:var(--white);border:1px solid #8ab8d6;font-size:13px;color:#555;padding:20px 12px}
.send-btn{position:absolute;left:496px;top:395px;width:207px;height:60px;border:1px solid var(--white);color:var(--white);font-size:17px;display:flex;align-items:center;justify-content:center;text-transform:uppercase}

/* footer */
.site-footer{top:2730px;height:250px}
.footer-col{position:absolute;top:52px;width:240px}
.footer-col h4{font-weight:900;font-size:24px;color:#333}
.footer-col h4 em{font-style:normal;color:var(--blue)}
.footer-col p{font-size:14px;line-height:25px;color:var(--grey)}
.footer-about p{margin-top:26px;width:230px}
.read-more{font-size:14px;font-weight:700;color:#333;text-decoration:underline;text-transform:uppercase}
.contact-line{display:flex;gap:14px;margin-top:24px}
.contact-line svg{flex:none;margin-top:4px}
.social{display:flex;gap:8px;margin-top:26px}
.social span{width:46px;height:46px;border:1px solid #9b9b9b;border-radius:50%}
.copyright{position:absolute;left:0;top:2980px;width:1200px;height:86px;background:var(--blue);color:var(--white);font-size:13px;display:flex;align-items:center;justify-content:center}
.copyright b{margin:0 4px}
</style>
</head>
<body>

<header class="site-header">
  <div class="brand"><span class="brand-mark"></span><span class="brand-name">BRIGHTLINE LABS</span></div>
  <nav class="main-nav"><a href="#">Home</a><a href="#">About</a><a href="#">Services</a><a href="#">Blog</a><a href="#">Contact</a></nav>
  <span class="nav-divider"></span>
  <div class="nav-phone">
    <svg width="20" height="20" viewBox="0 0 24 24"><path fill="#1784c7" d="M6.6 10.8a15.1 15.1 0 0 0 6.6 6.6l2.2-2.2c.3-.3.7-.4 1-.2 1.1.4 2.3.6 3.6.6.6 0 1 .4 1 1V20c0 .6-.4 1-1 1A17 17 0 0 1 3 4c0-.6.4-1 1-1h3.5c.6 0 1 .4 1 1 0 1.3.2 2.5.6 3.6.1.3 0 .7-.2 1z"/></svg>
    <span>555-204-7316</span>
  </div>
  <div class="login-btn">
    <svg width="18" height="18" viewBox="0 0 24 24" fill="none" stroke="#fff" stroke-width="2.4"><path d="M10 7l5 5-5 5M3 12h12M14 3h5a2 2 0 0 1 2 2v14a2 2 0 0 1-2 2h-5"/></svg>
    <span>Login</span>
  </div>
</header>

<section class="hero">
  <div class="hero-photo" role="img" aria-label="Photo of a team of analysts at laptops layered over a night city skyline with network lines"></div>
  <h1 class="hero-title">BRIGHTLINE LABS</h1>
  <p class="hero-text">Lorem Ipsum is simply dummy text of the printing and typesetting industry. Lorem Ipsum has been the industry's standard dummy text ever since the 1500s,</p>
  <div class="hero-actions"><span class="btn btn-solid">Contact Us</span><span class="btn btn-light">Learn More</span></div>
</section>

<section class="about">
  <h2 class="section-heading"><span>About <em>BRIGHTLINE LABS</em></span></h2>
  <p class="about-text">Lorem Ipsum is simply dummy text of the printing and typesetting industry. Lorem Ipsum has been the industry's standard dummy text ever since the 1500s, when an unknown printer took a galley of type and scrambled it to make a type specimen book. It has survived not only five centuries, but also the leap into electronic typesetting, remaining essentially unchanged.</p>
  <span class="btn btn-solid">Learn More</span>
</section>

<section class="services">
  <div class="services-bg" role="img" aria-label="Dark background photo of glowing data screens"></div>
  <h2 class="section-heading"><span>Our SERVICES</span></h2>

  <div class="service" style="left:79px">
    <svg width="160" height="150" viewBox="0 0 160 150"><circle cx="75" cy="78" r="64" fill="none" stroke="#1784c7" stroke-width="14"/><circle cx="75" cy="78" r="46" fill="#fff"/><circle cx="122" cy="34" r="11" fill="#2a9ad8"/><circle cx="142" cy="22" r="6" fill="#2a9ad8"/><g fill="none" stroke="#111" stroke-width="2.5"><rect x="55" y="60" width="40" height="24" rx="5"/><circle cx="66" cy="72" r="5"/><path d="M78 69h10M78 75h10M70 84l-4 14h18l-4-14M62 98h26"/></g></svg>
    <h3>Machine learning</h3>
    <p>Lorem Ipsum is simply dummy printing and typesetting industry.</p>
  </div>
  <div class="service" style="left:344px">
    <svg width="160" height="150" viewBox="0 0 160 150"><circle cx="75" cy="78" r="64" fill="none" stroke="#1784c7" stroke-width="14"/><circle cx="75" cy="78" r="46" fill="#fff"/><circle cx="122" cy="34" r="11" fill="#2a9ad8"/><circle cx="142" cy="22" r="6" fill="#2a9ad8"/><g fill="none" stroke="#111" stroke-width="2.5"><path d="M58 82a10 10 0 0 1 2-20 14 14 0 0 1 27-2 11 11 0 0 1 5 22z"/><circle cx="64" cy="96" r="4"/><circle cx="75" cy="100" r="4"/><circle cx="86" cy="96" r="4"/><path d="M66 82l-1 10M75 82v14M84 82l1 10"/></g></svg>
    <h3>Big data</h3>
    <p>Lorem Ipsum is simply dummy printing and typesetting industry.</p>
  </div>
  <div class="service" style="left:615px">
    <svg width="160" height="150" viewBox="0 0 160 150"><circle cx="75" cy="78" r="64" fill="none" stroke="#1784c7" stroke-width="14"/><circle cx="75" cy="78" r="46" fill="#fff"/><circle cx="122" cy="34" r="11" fill="#2a9ad8"/><circle cx="142" cy="22" r="6" fill="#2a9ad8"/><g fill="none" stroke="#111" stroke-width="2.5"><rect x="60" y="63" width="30" height="30" rx="3"/><circle cx="75" cy="78" r="7"/><path d="M68 63v-8M82 63v-8M68 93v8M82 93v8M60 71h-8M60 85h-8M90 71h8M90 85h8"/></g></svg>
    <h3>Data science</h3>
    <p>Lorem Ipsum is simply dummy printing and typesetting industry.</p>
  </div>
  <div class="service" style="left:884px">
    <svg width="160" height="150" viewBox="0 0 160 150"><circle cx="75" cy="78" r="64" fill="none" stroke="#1784c7" stroke-width="14"/><circle cx="75" cy="78" r="46" fill="#fff"/><circle cx="122" cy="34" r="11" fill="#2a9ad8"/><circle cx="142" cy="22" r="6" fill="#2a9ad8"/><g fill="none" stroke="#111" stroke-width="2.5"><path d="M52 100h46"/><rect x="57" y="84" width="7" height="16"/><rect x="68" y="78" width="7" height="22"/><rect x="79" y="72" width="7" height="28"/><path d="M56 74l12-10 10 6 16-14"/></g></svg>
    <h3>Data analytics</h3>
    <p>Lorem Ipsum is simply dummy printing and typesetting industry.</p>
  </div>
</section>

<section class="blog">
  <h2 class="section-heading"><span>Recent <em>BLOG</em></span></h2>
  <article class="post" style="left:78px">
    <div class="post-meta">July 03 , 2018<span>/</span>3 Comments</div>
    <h3>Lorem Ipsum printing and typesetting industry.</h3>
    <p>Lorem Ipsum is simply dummy text of the printing and typesetting industry. Lorem Ipsum has been the industry's</p>
    <hr>
    <div class="author"><div class="avatar" role="img" aria-label="Author portrait"></div><span>By Mira Olsen</span></div>
  </article>
  <article class="post" style="left:444px">
    <div class="post-meta">July 03 , 2018<span>/</span>3 Comments</div>
    <h3>Lorem Ipsum printing and typesetting industry.</h3>
    <p>Lorem Ipsum is simply dummy text of the printing and typesetting industry. Lorem Ipsum has been the industry's</p>
    <hr>
    <div class="author"><div class="avatar" role="img" aria-label="Author portrait"></div><span>By Lena Vogt</span></div>
  </article>
  <article class="post" style="left:810px">
    <div class="post-meta">July 03 , 2018<span>/</span>3 Comments</div>
    <h3>Lorem Ipsum printing and typesetting industry.</h3>
    <p>Lorem Ipsum is simply dummy text of the printing and typesetting industry. Lorem Ipsum has been the industry's</p>
    <hr>
    <div class="author"><div class="avatar" role="img" aria-label="Author portrait"></div><span>By Ravi Maren</span></div>
  </article>
</section>

<section class="contact">
  <div class="contact-photo" role="img" aria-label="Blue-toned photo of a consultant in a suit working on a tablet"></div>
  <h2 class="section-heading"><span>Contact US</span></h2>
  <div class="field" style="left:141px;top:135px;width:294px;height:62px">Name :</div>
  <div class="field" style="left:454px;top:135px;width:293px;height:62px">Phone :</div>
  <div class="field" style="left:766px;top:135px;width:293px;height:62px">Email :</div>
  <div class="field" style="left:141px;top:217px;width:918px;height:158px;padding-top:16px">Message :</div>
  <div class="send-btn">Send Message</div>
</section>

<footer class="site-footer">
  <div class="footer-col footer-about" style="left:78px">
    <h4>About <em>US</em></h4>
    <p>Lorem Ipsum is simply dummy the text of the printing and Printing of typesetting industry. Lorem Ipsum</p>
    <span class="read-more">Read More</span>
  </div>
  <div class="footer-col" style="left:343px">
    <h4>Office <em>ADDRESS</em></h4>
    <div class="contact-line">
      <svg width="16" height="20" viewBox="0 0 16 20"><path fill="#1784c7" d="M8 0a7 7 0 0 0-7 7c0 5 7 13 7 13s7-8 7-13a7 7 0 0 0-7-7zm0 10a3 3 0 1 1 0-6 3 3 0 0 1 0 6z"/></svg>
      <p>48 Harbor Crest Avenue<br>Suite 210 Lakeview, OR<br>97630</p>
    </div>
  </div>
  <div class="footer-col" style="left:608px">
    <h4>Call <em>US</em></h4>
    <div class="contact-line">
      <svg width="20" height="20" viewBox="0 0 24 24"><path fill="#1784c7" d="M6.6 10.8a15.1 15.1 0 0 0 6.6 6.6l2.2-2.2c.3-.3.7-.4 1-.2 1.1.4 2.3.6 3.6.6.6 0 1 .4 1 1V20c0 .6-.4 1-1 1A17 17 0 0 1 3 4c0-.6.4-1 1-1h3.5c.6 0 1 .4 1 1 0 1.3.2 2.5.6 3.6.1.3 0 .7-.2 1z"/></svg>
      <p>555-204-7316</p>
    </div>
    <div class="contact-line" style="margin-top:10px">
      <svg width="20" height="16" viewBox="0 0 20 16"><path fill="#1784c7" d="M0 0h20v16H0z"/><path d="M1 1l9 7 9-7" fill="none" stroke="#fff" stroke-width="1.6"/></svg>
      <p>hello@brightlinelabs.example</p>
    </div>
  </div>
  <div class="footer-col" style="left:873px">
    <h4>Follow <em>ON</em></h4>
    <div class="social"><span></span><span></span><span></span><span></span></div>
  </div>
</footer>

<div class="copyright">Copyright ©<b>BRIGHTLINE LABS</b>- 2018 . All Right Reserved</div>

</body>
</html>
```